New Corporate Email Signature with Custom GIF KAV Electric LLC & KAV Fire & Security

Project Overview
KAV Electric LLC and KAV Fire & Security are seeking a professional, polished, and technically robust corporate email signature design. The project has two integrated deliverables:
A custom animated GIF representing both sides of our business
A complete corporate email signature layout designed for real-world compatibility (Gmail, Outlook, iOS, Android)
Our brand aesthetic is corporate, conservative, and clean. We value clarity, trust, professionalism, and subtle creativity β€” nothing overly flashy or cartoonish.
This design will be used across the entire company and must be visually aligned with our brand while remaining technically dependable.

PART 1 β€” Animated GIF Requirements
The GIF will be the core visual anchor of the new signature.
It must be clean, smooth, subtle, and optimized for email use.
βš™ Technical Requirements
Max file size: 150–200 KB (smaller is better)
Dimensions: approx 300px width (flexible, but must look good small)
Looping: continuous loop
Style: professional, minimalistic transitions

No rapid flashing or harsh animations
Must export cleanly into a format email clients accept

🎞 GIF Animation Sequence
Phase 1 β€” KAV Electric (KE)
Use the yellow β€œKE” avatar logo (provided).
Animation flow:
KE avatar appears
Full name β€œKAV Electric LLC” slides in, fades in, or otherwise appears smoothly
A scrolling or cycling list of service offerings displays:
EV Charging Stations
Generator & Transformers
Testing & Troubleshooting
LED Lighting Upgrades
After the list is shown, the entire KE segment fades out

Phase 2 β€” KAV Fire & Security (KF)
Use the red β€œKF” avatar logo (provided).
Animation flow mirrors Phase 1:
KF avatar appears
Full name β€œKAV Fire & Security” slides/fades in
Scrolling or cycling list of services displays:
Fire Alarm Upgrades
BQTL 48 Test & Inspect
Security Surveillance Systems
Access Control Systems
Data & Fiber Optic Cabling
Fade out β†’ loop back to KE
Creative Direction

Designers are encouraged to use:
Clean transitions
Soft fades
Professional typography
Modern minimalism
Consistent brand colors
High clarity at small sizes

Avoid:
Busy motion
Hard flashes
Excessive text overlays
Overly long transitions

The goal: a smooth, corporate-grade rotation that fits seamlessly into an email signature.

PART 2 β€” Corporate Email Signature Design

The signature must be visually appealing, brand-aligned, and structurally bulletproof across all major email systems.
πŸ“ Required Elements
πŸ‘€ Left Side Content
Circular headshot (we will supply final photos)
Social media icons with embedded URLs:
Facebook
LinkedIn
Google Business Profile
Instagram

Icons should be clean, modern, and in alignment with brand colors
πŸ“„ Right Side Content
Name
Title
KAV Electric LLC / KAV Fire & Security (depending on user)
Phone number
Email address
License# 52804
Physical office address: 384 Pembrook St, Westwood NJ 07912

Small CTA for newsletter signup (button or micro-banner)

🏒 Branding Assets Provided

You will receive:
KE avatar logo
KF avatar logo
Full-name KE logo
Full-name KF logo

These should be incorporated naturally and professionally.

Design Requirements

Conservative corporate styling

Clean typography

Balanced use of white space

Professional hierarchy

Light and dark mode compatibility preferred

Layout should not rely on one large image

All images should export cleanly for hosting on servers/CDN

Avoid overly tall signatures

The final signature must present as modern, trustworthy, and technically reliable across platforms.

πŸ§ͺ Compatibility Requirements

The signature must display correctly in:

Gmail (web and mobile)

Outlook (desktop & online)

Apple Mail

iPhone Mail

Android mail apps

Designers must avoid DIV-based layouts and instead propose a layout that can be implemented using table-based HTML, which is the industry standard for email compatibility.

You do not need to build the HTML β€” only supply the final layered design (PSD/AI/Figma) plus a clear structural layout that can be converted to HTML later.

πŸ“¦ Deliverables
1. Animated GIF

Final optimized GIF

Source file (After Effects, Photoshop, or equivalent)

Export guidelines so we can reproduce future versions

2. Email Signature Design

Full static design mockup

Modular layout for each employee

Icon set for social media

Newsletter CTA element

Clear spacing, alignment, and typography specifications

All source files (PSD, AI, Figma, etc.)

🧭 Creative Guidance Summary

We want:
βœ” Modern
βœ” Corporate
βœ” Minimalistic
βœ” Professional
βœ” Clean motion
βœ” Consistent branding
βœ” Email-safe elements

We do not want:
✘ Flashy marketing look
✘ Overly colorful or playful styles
✘ Hard-to-read fonts
✘ Heavy animation
✘ Oversized signatures

πŸ›  Tools & Format Flexibility

We allow full creative freedom regarding:

Animation style

Typography choices

Structuring of the two-column layout

How the service lists scroll or cycle

As long as the end result is clean, brand-aligned, professional, and email-compatible.

πŸ’¬ Final Note to Designers

We encourage creativity within the boundaries of corporate professionalism.
This signature will represent our company every time an email is sent β€” it must communicate trust, clarity, expertise, and brand strength.

```html
<!DOCTYPE html>
<html lang="en">
<head>
<meta charset="UTF-8">
<title>KAV Email Signatures</title>
<link rel="stylesheet" href="https://fonts.googleapis.com/css2?family=Inter:wght@600;700&family=Poppins:wght@300;400;500;600;700&family=Open+Sans:wght@700&display=swap">
<style>
  :root {
    --page-bg: #d9d9d9;
    --card-bg: #ffffff;
    --ink: #2e2e2e;
    --muted: #7a7a7a;
    --rule: #8a8a8a;
    --electric: #d6b11f;
    --electric-text: #d8b31a;
    --fire: #e0202c;
    --fire-text: #e11d2a;
    --social: #2a6fb8;
    --caption: #333333;
  }
  * { margin: 0; padding: 0; box-sizing: border-box; }
  html, body { width: 1200px; height: 967px; overflow: hidden; }
  body {
    background: var(--page-bg);
    position: relative;
    font-family: "Poppins", sans-serif;
    color: var(--ink);
  }

  .card {
    position: absolute;
    left: 63px;
    width: 1073px;
    height: 380px;
    background: var(--card-bg);
    box-shadow: 0 14px 30px rgba(0,0,0,0.12);
    --brand: var(--electric);
    --brand-text: var(--electric-text);
  }
  .card--electric { top: 53px; }
  .card--fire { top: 507px; --brand: var(--fire); --brand-text: var(--fire-text); }

  .headshot {
    position: absolute;
    left: 44px; top: 49px;
    width: 161px; height: 161px;
    border-radius: 50%;
  }
  .card--electric .headshot { background: radial-gradient(circle at 50% 40%, #e9e4e6 0%, #d8d2d6 55%, #2b3245 100%); }
  .card--fire .headshot { background: radial-gradient(circle at 50% 40%, #f2efec 0%, #e2dcd6 55%, #9a8f88 100%); }

  .identity { position: absolute; left: 226px; top: 38px; }
  .identity__name {
    font-family: "Inter", sans-serif;
    font-weight: 700;
    font-size: 32px;
    line-height: 40px;
    color: var(--muted);
    letter-spacing: -0.2px;
  }
  .identity__title {
    font-family: "Inter", sans-serif;
    font-weight: 600;
    font-size: 19.5px;
    line-height: 26px;
    color: var(--ink);
  }
  .identity__org { color: var(--muted); }
  .identity__division { color: var(--brand-text); }

  .social {
    position: absolute;
    left: 904px; top: 78px;
    display: flex; gap: 11px;
    list-style: none;
  }
  .social__item {
    width: 20px; height: 20px;
    border-radius: 50%;
    background: var(--social);
  }

  .rule {
    position: absolute;
    left: 226px; top: 109px;
    width: 796px; height: 1px;
    background: var(--rule);
  }

  .contact {
    position: absolute;
    left: 226px; top: 128px;
    list-style: none;
  }
  .contact__row {
    font-size: 19.5px;
    font-weight: 300;
    line-height: 34px;
    color: #555;
    white-space: nowrap;
  }
  .contact__label { color: var(--brand-text); font-weight: 400; margin-right: 4px; }
  .contact__key { color: var(--ink); font-weight: 500; }

  .brand {
    position: absolute;
    left: 780px; top: 150px;
    width: 245px;
    text-align: center;
  }
  .brand__mark {
    display: inline-flex; align-items: center; gap: 10px;
  }
  .brand__square {
    width: 34px; height: 34px;
    background: var(--brand);
  }
  .brand__name {
    font-weight: 700;
    font-size: 21px;
    color: var(--muted);
    letter-spacing: 0.3px;
  }
  .brand__service {
    margin-top: 22px;
    font-weight: 600;
    font-size: 16.5px;
    color: var(--muted);
  }

  .newsletter {
    position: absolute;
    left: 48px; top: 276px;
    width: 978px; height: 78px;
    border-radius: 12px;
    background: var(--brand);
    overflow: hidden;
  }
  .newsletter__gallery {
    position: absolute;
    left: 329px; top: 0;
    width: 649px; height: 100%;
  }
  .card--electric .newsletter__gallery {
    background: linear-gradient(90deg, rgba(214,177,31,0) 0%, #8a8463 22%, #5b6168 40%, #9aa36a 58%, #7d7b6e 75%, #3c3f46 100%);
  }
  .card--fire .newsletter__gallery {
    background: linear-gradient(90deg, rgba(224,32,44,0) 0%, #9b6a6c 22%, #5b6168 40%, #7a6a56 58%, #86605a 75%, #6d1f22 100%);
  }
  .newsletter__button {
    position: absolute;
    left: 73px; top: 24px;
    width: 209px; height: 33px;
    border: 1.5px solid #ffffff;
    border-radius: 17px;
    font-family: "Open Sans", sans-serif;
    font-weight: 700;
    font-size: 15.5px;
    line-height: 30px;
    color: #ffffff;
    text-align: center;
  }

  .caption {
    position: absolute;
    left: 0; width: 1200px;
    text-align: center;
    font-size: 11px;
    color: var(--caption);
  }
  .caption--electric { top: 442px; }
  .caption--fire { top: 900px; }
</style>
</head>
<body>

  <section class="card card--electric">
    <div class="headshot" role="img" aria-label="Circular headshot of the employee"></div>
    <div class="identity">
      <h1 class="identity__name">Daniel Reyes</h1>
      <p class="identity__title">Project Manager, <span class="identity__org">KAV</span> <span class="identity__division">Electric LLC</span></p>
    </div>
    <ul class="social" aria-label="Social links">
      <li class="social__item" aria-label="Social profile 1"></li>
      <li class="social__item" aria-label="Social profile 2"></li>
      <li class="social__item" aria-label="Social profile 3"></li>
      <li class="social__item" aria-label="Social profile 4"></li>
    </ul>
    <div class="rule"></div>
    <ul class="contact">
      <li class="contact__row"><span class="contact__label">P :</span> 201-555-0148</li>
      <li class="contact__row"><span class="contact__label">E :</span> daniel.reyes@kavelectric.com</li>
      <li class="contact__row"><span class="contact__key">License</span> # 52804</li>
      <li class="contact__row"><span class="contact__key">Office</span> 384 Pembrook St, Westwood NJ 07912</li>
    </ul>
    <div class="brand">
      <div class="brand__mark"><span class="brand__square"></span><span class="brand__name">KAV Electric LLC</span></div>
      <p class="brand__service">EV Charging Stations</p>
    </div>
    <div class="newsletter">
      <div class="newsletter__gallery" role="img" aria-label="Photo strip of service vans, technicians and electrical equipment"></div>
      <span class="newsletter__button">Join Our Newsletter</span>
    </div>
  </section>
  <p class="caption caption--electric">Animation Start - KAV Electric</p>

  <section class="card card--fire">
    <div class="headshot" role="img" aria-label="Circular headshot of the employee"></div>
    <div class="identity">
      <h1 class="identity__name">Daniel Reyes</h1>
      <p class="identity__title">Project Manager, <span class="identity__org">KAV</span> <span class="identity__division">Fire &amp; Security</span></p>
    </div>
    <ul class="social" aria-label="Social links">
      <li class="social__item" aria-label="Social profile 1"></li>
      <li class="social__item" aria-label="Social profile 2"></li>
      <li class="social__item" aria-label="Social profile 3"></li>
      <li class="social__item" aria-label="Social profile 4"></li>
    </ul>
    <div class="rule"></div>
    <ul class="contact">
      <li class="contact__row"><span class="contact__label">P :</span> 201-555-0148</li>
      <li class="contact__row"><span class="contact__label">E :</span> daniel.reyes@kavelectric.com</li>
      <li class="contact__row"><span class="contact__key">License</span> # 52804</li>
      <li class="contact__row"><span class="contact__key">Office</span> 384 Pembrook St, Westwood NJ 07912</li>
    </ul>
    <div class="brand">
      <div class="brand__mark"><span class="brand__square"></span><span class="brand__name">KAV Fire &amp; Security</span></div>
      <p class="brand__service">Fire Alarm Upgrades</p>
    </div>
    <div class="newsletter">
      <div class="newsletter__gallery" role="img" aria-label="Photo strip of service vans, technicians, interiors and fire alarm panels"></div>
      <span class="newsletter__button">Join Our Newsletter</span>
    </div>
  </section>
  <p class="caption caption--fire">Animation Start - KAV Fire &amp; Secu.</p>

</body>
</html>
```